Dynamic Business Card for Sports Supplements Company

Hi! I'm looking for an awesome business card to match my existing sports supplement company. I have uploaded my current company logo and screenshot of the front page of my website.

I would like to have something dynamic and interesting and utilize the colors in the website - the reds and purples

The business card should be double sided and focus on a unique eye-catching design on the back and include all the relevant company info.

Most importantly, it should say somewhere: "Sign up on our website for a coupon code."

Target Market(s)

Mostly for women gym goers but it shouldn't be too feminine. It should be in keeping with the website design. It should flow and clearly be connected to it

Industry/Entity Type

Business

Contact Information for Business Card

Lorraine K. Vestal
CEO
LVestal@Quorvanexco.com
www.quorvanexco.com
555.417.3820
P.O. Box 47315
Harlow, Vermont 00000

Sign up on our website for a coupon code

Font styles to use
Serif
Sans Serif
Other font styles liked:
• Novecento font family and "Quorvanex" is in AR Destine font

Requirements
Must have
• One side should be a bold Quorvanex logo design. Even just the symbol itself may be o.k. (see attached file)

```html
<!DOCTYPE html>
<html lang="en">
<head>
<meta charset="utf-8">
<title>Quorvanex Business Card</title>
<link rel="stylesheet" href="https://fonts.googleapis.com/css2?family=Figtree:wght@400;500;800&display=swap">
<style>
  :root {
    --stage: #3b3b3d;
    --card-black: #000000;
    --brand-red: #ec1c24;
    --paper: #ffffff;
    --ink: #111111;
  }
  * { margin: 0; padding: 0; box-sizing: border-box; }
  html, body { width: 1200px; height: 855px; overflow: hidden; }
  body {
    background: var(--stage);
    font-family: "Figtree", Arial, sans-serif;
    position: relative;
  }
  .card {
    position: absolute;
    left: 354px;
    width: 493px;
    overflow: hidden;
  }
  /* Back side */
  .card-back {
    top: 137px;
    height: 280px;
    background: var(--card-black);
    color: var(--paper);
  }
  .back-emblem {
    position: absolute;
    left: 190px; top: 84px;
    width: 114px; height: 114px;
    border: 6px solid var(--paper);
    border-radius: 50%;
    display: flex; align-items: center; justify-content: center;
  }
  .back-emblem-name {
    font-weight: 800;
    font-size: 12px;
    letter-spacing: 0.4px;
    color: var(--paper);
  }
  .back-offer {
    position: absolute;
    left: 0; right: 0; top: 236px;
    text-align: center;
    font-size: 12.5px;
    font-weight: 400;
  }
  /* Front side */
  .card-front {
    top: 430px;
    height: 288px;
    background: var(--paper);
  }
  .front-shapes { position: absolute; inset: 0; width: 100%; height: 100%; }
  .contact-block {
    position: absolute;
    left: 26px; top: 120px;
    color: var(--paper);
  }
  .holder-name { font-size: 18px; font-weight: 500; line-height: 1.1; }
  .holder-title { font-size: 13px; line-height: 1.3; margin-bottom: 14px; }
  .address { font-size: 13px; line-height: 1.3; margin-bottom: 12px; }
  .contact-line { font-size: 13px; line-height: 1.3; display: flex; align-items: center; gap: 5px; }
  .contact-line svg { width: 11px; height: 11px; flex: none; }
  .brand-lockup {
    position: absolute;
    left: 300px; top: 27px;
    width: 170px;
    text-align: center;
  }
  .brand-dot {
    width: 52px; height: 52px;
    border-radius: 50%;
    background: var(--brand-red);
    margin: 0 auto 10px;
  }
  .brand-name {
    font-weight: 800;
    font-size: 24px;
    letter-spacing: 1px;
    color: var(--ink);
    line-height: 1;
  }
  .brand-tagline {
    font-size: 8.6px;
    letter-spacing: 0.7px;
    color: var(--ink);
    margin-top: 3px;
  }
</style>
</head>
<body>
  <section class="card card-back">
    <div class="back-emblem"><span class="back-emblem-name">QUORVANEX</span></div>
    <p class="back-offer">Sign up on our website for a coupon code</p>
  </section>

  <section class="card card-front">
    <svg class="front-shapes" viewBox="0 0 616 360" preserveAspectRatio="none" aria-hidden="true">
      <polygon points="0,0 208,0 398,360 0,360" fill="var(--brand-red)"/>
      <polygon points="208,0 216,0 406,360 398,360" fill="var(--ink)"/>
    </svg>

    <div class="contact-block">
      <p class="holder-name">Lorraine K. Vestal</p>
      <p class="holder-title">CEO</p>
      <p class="address">P.O. Box 47315<br>Harlow, Vermont 00000</p>
      <p class="contact-line">
        <svg viewBox="0 0 12 12"><path d="M2 1 L4 1 L5 4 L3.5 5 Q5 8 7 8.5 L8 7 L11 8 L11 10 Q10 11 8 11 Q1 9 1 2 Z" fill="var(--paper)"/></svg>
        555.417.3820
      </p>
      <p class="contact-line">
        <svg viewBox="0 0 12 12"><rect x="1" y="3" width="10" height="7" fill="none" stroke="var(--paper)" stroke-width="1.2"/><path d="M1 3 L6 7 L11 3" fill="none" stroke="var(--paper)" stroke-width="1.2"/></svg>
        LVestal@Quorvanexco.com
      </p>
      <p class="contact-line">
        <svg viewBox="0 0 12 12"><circle cx="6" cy="6" r="5" fill="none" stroke="var(--paper)" stroke-width="1"/><ellipse cx="6" cy="6" rx="2.2" ry="5" fill="none" stroke="var(--paper)" stroke-width="1"/><path d="M1 6 H11 M2 3.5 H10 M2 8.5 H10" stroke="var(--paper)" stroke-width="0.8"/></svg>
        www.quorvanexco.com
      </p>
    </div>

    <div class="brand-lockup">
      <div class="brand-dot"></div>
      <p class="brand-name">QUORVANEX</p>
      <p class="brand-tagline">YOUR STRENGTH COMPANION</p>
    </div>
  </section>
</body>
</html>
```